TL - business card

Tallow Partners is an insurance brokerage firm, inovative, proactive, vigorous, which aims to become the leader of the insurance brokers in Anfrica. We should like to get some designs which should be avoided also in Gray / Metallic for the Administration and Orange / Blue for the Managers (ike in the picture sent). The Blue / Green logo is not the correct one, but the source of the file. Please adjust the color accordingly for the business cards. 1 / Orange / Blue 2 / Gray / Metallic We want something classic but which is transmitted strenght, inovation, modernity and most of all, rapidity. We want something start-up like, very punchy and catching eye remaining profesional at the same time. Name: Dorian Whitlock Function: Managing Director Address: N ° 17/18 Rua Veloso - R / C 2B Direita - Bairro Mutamba - Luanda Tel: (+244) 947 582 316 Email: dorian.whitlock@tallow-p.example Website: www.tallow-p. example We want classic in the front and creative, colorfull at the back. The cards will be printed in relief, with very high quality of paper.
Insurance Broker
Colors
Designer to choose colors to be used in the design.

```html
<!DOCTYPE html>
<html lang="en">
<head>
<meta charset="utf-8">
<title>Tallow Partners – Business Card</title>
<link href="https://fonts.googleapis.com/css2?family=Lato:wght@400;700&display=swap" rel="stylesheet">
<style>
  :root {
    --brand-blue: #1a7fc4;
    --brand-blue-dark: #1570b0;
    --brand-orange: #e8821e;
    --ink: #2b2b2b;
    --card-white: #f6f6f6;
    --canvas-bg: #e4e4e4;
  }
  * { margin: 0; padding: 0; box-sizing: border-box; }
  html, body {
    width: 1200px; height: 1021px; overflow: hidden;
    background: var(--canvas-bg);
    font-family: "Lato", sans-serif;
  }
  .stage { position: relative; width: 1200px; height: 1021px; }
  .card {
    position: absolute; left: 250px; width: 700px; height: 400px;
    box-shadow: 0 6px 18px rgba(0,0,0,0.18);
  }
  .card-back {
    top: 80px;
    background: linear-gradient(180deg, var(--brand-blue) 0%, var(--brand-blue-dark) 100%);
    display: flex; align-items: center; justify-content: center; gap: 18px;
  }
  .back-mark {
    width: 34px; height: 34px; border-radius: 50%;
    background: var(--brand-orange);
  }
  .back-name {
    color: #ffffff; font-weight: 700; font-size: 40px; letter-spacing: 1px;
    text-transform: uppercase;
  }
  .card-front { top: 540px; background: var(--card-white); }
  .front-brand {
    position: absolute; left: 50px; top: 150px; width: 260px;
    display: flex; align-items: center; gap: 12px;
  }
  .front-mark { width: 22px; height: 22px; border-radius: 50%; background: var(--brand-orange); flex: none; }
  .front-name {
    color: var(--brand-blue); font-weight: 700; font-size: 27px;
    text-transform: uppercase; line-height: 1.05;
  }
  .divider {
    position: absolute; left: 335px; top: 118px; width: 2px; height: 150px;
    background: #555;
  }
  .contact { position: absolute; left: 365px; top: 118px; color: var(--ink); }
  .person-name { color: var(--brand-blue); font-weight: 700; font-size: 27px; line-height: 1.05; }
  .person-role { font-size: 19px; margin-bottom: 10px; }
  .contact-line { display: flex; align-items: center; gap: 8px; font-size: 18px; line-height: 1.35; }
  .contact-line svg { width: 15px; height: 15px; flex: none; }
  .address {
    position: absolute; left: 50px; right: 30px; top: 318px;
    font-size: 19.5px; color: var(--ink); letter-spacing: 0.2px;
  }
</style>
</head>
<body>
<div class="stage">
  <section class="card card-back" aria-label="Card back">
    <span class="back-mark"></span>
    <span class="back-name">Tallow Partners</span>
  </section>

  <section class="card card-front" aria-label="Card front">
    <div class="front-brand">
      <span class="front-mark"></span>
      <span class="front-name">Tallow Partners</span>
    </div>
    <div class="divider"></div>
    <div class="contact">
      <div class="person-name">Dorian Whitlock</div>
      <div class="person-role">Managing Director</div>
      <div class="contact-line">
        <svg viewBox="0 0 16 16"><path d="M3 1.5l3 3-1.6 1.8c.9 2 2.4 3.5 4.3 4.3L10.5 9l3 3-2 2.5C6 14 2 10 1.5 3.5z" fill="var(--brand-orange)"/></svg>
        (+244) 947 582 316
      </div>
      <div class="contact-line">
        <svg viewBox="0 0 16 16"><rect x="1" y="3" width="14" height="10" fill="none" stroke="var(--brand-orange)" stroke-width="1.6"/><path d="M1 3l7 6 7-6" fill="none" stroke="var(--brand-orange)" stroke-width="1.6"/></svg>
        dorian.whitlock@tallow-p.example
      </div>
      <div class="contact-line">
        <svg viewBox="0 0 16 16"><circle cx="8" cy="8" r="6.5" fill="none" stroke="var(--brand-orange)" stroke-width="1.4"/><ellipse cx="8" cy="8" rx="3" ry="6.5" fill="none" stroke="var(--brand-orange)" stroke-width="1.2"/><path d="M1.5 8h13" stroke="var(--brand-orange)" stroke-width="1.2"/></svg>
        www.tallow-p. example
      </div>
    </div>
    <p class="address">N ° 17/18 Rua Veloso - R / C 2B Direita - Bairro Mutamba - Luanda</p>
  </section>
</div>
</body>
</html>
```